Company identity deisgn should support 2 languages

I would like to get our company identity design
This includes the following only
Business Cards 2 languages Arabic and English
Email signature
Letterhead
Linkedin profile images
Attached is the logo in Ai format

Requirements
Must have
• For business card
Must have
Name and Adrees in arabic
Name and Address in english
You might use both side of the card
Should not have
• Any pictures other than the logo

```html
<!DOCTYPE html>
<html lang="en">
<head>
<meta charset="utf-8">
<title>Northwind Systems – Business Cards</title>
<link href="https://fonts.googleapis.com/css2?family=Poppins:wght@400;500;600&family=Noto+Sans+Arabic:wght@400;600&display=swap" rel="stylesheet">
<style>
  :root {
    --backdrop: #8e8e8e;
    --card: #ffffff;
    --brand-blue: #1177c0;
    --wave-grey: #b9b9bc;
    --on-blue: #ffffff;
  }
  * { box-sizing: border-box; margin: 0; padding: 0; }
  html, body { width: 1200px; height: 1200px; overflow: hidden; }
  body {
    background: var(--backdrop);
    font-family: "Poppins", sans-serif;
    position: relative;
  }
  .card {
    position: absolute;
    left: 257px;
    width: 686px;
    height: 392px;
    background: var(--card);
    border-radius: 22px;
    overflow: hidden;
  }
  .card--english { top: 165px; }
  .card--arabic { top: 653px; }
  .card__wave { position: absolute; inset: 0; width: 100%; height: 100%; }
  .brand {
    position: absolute;
    top: 112px;
    left: 0; right: 0;
    display: flex;
    justify-content: center;
    align-items: center;
    gap: 14px;
  }
  .brand__mark { width: 36px; height: 36px; background: var(--brand-blue); }
  .brand__name {
    color: var(--brand-blue);
    font-weight: 500;
    font-size: 30px;
    letter-spacing: 1px;
  }
  .holder {
    position: absolute;
    left: 40px;
    top: 275px;
    color: var(--on-blue);
  }
  .holder__name { font-weight: 600; font-size: 23px; line-height: 1.2; letter-spacing: .3px; }
  .holder__title { font-size: 16px; line-height: 1.3; }
  .holder__address { margin-top: 8px; font-size: 16px; line-height: 1.25; }
  .holder--arabic {
    font-family: "Noto Sans Arabic", sans-serif;
    text-align: left;
  }
  .holder--arabic .holder__name { font-size: 22px; }
  .holder--arabic .holder__address { font-size: 15px; line-height: 1.45; }
  .contacts {
    position: absolute;
    right: 28px;
    top: 292px;
    list-style: none;
    color: var(--on-blue);
    font-size: 16px;
    line-height: 19.6px;
  }
  .contacts li { display: flex; justify-content: flex-end; align-items: center; gap: 10px; }
  .contacts svg { width: 13px; height: 13px; flex: none; }
</style>
</head>
<body>

<section class="card card--english" aria-label="Business card, English side">
  <svg class="card__wave" viewBox="0 0 800 457" preserveAspectRatio="none" aria-hidden="true">
    <path d="M0,282 C120,250 320,285 500,298 C650,308 740,268 800,222 L800,457 L0,457Z" fill="var(--wave-grey)"/>
    <path d="M0,290 C140,258 340,292 500,305 C650,316 740,274 800,228 L800,457 L0,457Z" fill="var(--brand-blue)"/>
  </svg>
  <div class="brand">
    <span class="brand__mark"></span>
    <span class="brand__name">NORTHWIND SYSTEMS</span>
  </div>
  <div class="holder">
    <p class="holder__name">DANIEL HARPER</p>
    <p class="holder__title">President</p>
    <p class="holder__address">2146 Willow Bend Road<br>Fairbanks, Alaska 99701</p>
  </div>
  <ul class="contacts">
    <li>555-014-2738 <svg viewBox="0 0 16 16"><path d="M3 1l3 0 1.5 4-2 1.3a9 9 0 0 0 4.2 4.2L11 8.5l4 1.5v3c0 1-1 2-2 2C7 15 1 9 1 3c0-1 1-2 2-2z" fill="#fff"/></svg></li>
    <li>555-019-6402 <svg viewBox="0 0 16 16"><rect x="4" y="1" width="8" height="14" rx="1.5" fill="none" stroke="#fff" stroke-width="1.8"/></svg></li>
    <li>info@northwindsystems.com <svg viewBox="0 0 16 16"><rect x="1" y="3.5" width="14" height="9" fill="#fff"/><path d="M1 3.5l7 5 7-5" fill="none" stroke="#1177c0" stroke-width="1.2"/></svg></li>
    <li>www.northwindsystems.com <svg viewBox="0 0 16 16"><circle cx="8" cy="8" r="7" fill="#fff"/><path d="M4 5c2 0 3 2 2 4M10 11c1-2 3-2 4-1" stroke="#1177c0" stroke-width="1.5" fill="none"/></svg></li>
  </ul>
</section>

<section class="card card--arabic" aria-label="Business card, Arabic side">
  <svg class="card__wave" viewBox="0 0 800 457" preserveAspectRatio="none" aria-hidden="true">
    <path d="M0,282 C120,250 320,285 500,298 C650,308 740,268 800,222 L800,457 L0,457Z" fill="var(--wave-grey)"/>
    <path d="M0,290 C140,258 340,292 500,305 C650,316 740,274 800,228 L800,457 L0,457Z" fill="var(--brand-blue)"/>
  </svg>
  <div class="brand">
    <span class="brand__mark"></span>
    <span class="brand__name">NORTHWIND SYSTEMS</span>
  </div>
  <div class="holder holder--arabic" dir="rtl" lang="ar">
    <p class="holder__name">دانيال هاربر</p>
    <p class="holder__title">رئيس</p>
    <p class="holder__address">2146 طريق ويلو بند<br>فيربانكس ، ألاسكا 99701</p>
  </div>
  <ul class="contacts" style="right:38px; top:286px;">
    <li>555-014-2738 <svg viewBox="0 0 16 16"><path d="M3 1l3 0 1.5 4-2 1.3a9 9 0 0 0 4.2 4.2L11 8.5l4 1.5v3c0 1-1 2-2 2C7 15 1 9 1 3c0-1 1-2 2-2z" fill="#fff"/></svg></li>
    <li>555-019-6402 <svg viewBox="0 0 16 16"><rect x="4" y="1" width="8" height="14" rx="1.5" fill="none" stroke="#fff" stroke-width="1.8"/></svg></li>
    <li>info@northwindsystems.com <svg viewBox="0 0 16 16"><rect x="1" y="3.5" width="14" height="9" fill="#fff"/><path d="M1 3.5l7 5 7-5" fill="none" stroke="#1177c0" stroke-width="1.2"/></svg></li>
    <li>www.northwindsystems.com <svg viewBox="0 0 16 16"><circle cx="8" cy="8" r="7" fill="#fff"/><path d="M4 5c2 0 3 2 2 4M10 11c1-2 3-2 4-1" stroke="#1177c0" stroke-width="1.5" fill="none"/></svg></li>
  </ul>
</section>

</body>
</html>
```